SkyvornQ Business Cards and Stationary Design

Need a design for our business cards and stationary. I want to carry on the theme of the logo. I want the business cards to have a design on the back. I would like the business cards and the stationary to carry the same theme, design scheme, and branding

Target Market(s)

Airlines and Maintenance Facilities

Industry/Entity Type

Aviation

Contact Information for Business Card

Name
Position Title
Address: 4827 Trellis Hollow Road, Brindlecove, Norvale 34951
Office Number
Mobile Number
Email
Website

Font styles to use
Serif
Sans Serif

Colors

Designer to choose colors to be used in the design.

```html
<!DOCTYPE html>
<html lang="en">
<head>
<meta charset="utf-8">
<title>SkyvornQ Business Card</title>
<link rel="stylesheet" href="https://fonts.googleapis.com/css2?family=Open+Sans:wght@400;600;700&display=swap">
<style>
  :root {
    --page: #d9d9d9;
    --navy: #142a52;
    --sky: #1f8fd6;
    --paper: #f7f7f7;
    --ink: #1b2d52;
    --muted: #5a6272;
  }
  * { box-sizing: border-box; margin: 0; padding: 0; }
  html, body { width: 1200px; height: 852px; overflow: hidden; }
  body {
    background: var(--page);
    font-family: "Open Sans", Arial, sans-serif;
    position: relative;
  }
  .card {
    position: absolute;
    width: 520px;
    height: 300px;
    border-radius: 22px;
    overflow: hidden;
  }
  .card-back {
    left: 90px; top: 110px;
    background: var(--navy);
    display: flex; align-items: center; justify-content: center; gap: 16px;
  }
  .card-back .brand-name { color: var(--sky); font-size: 46px; font-weight: 700; letter-spacing: 5px; }
  .card-back .brand-dot { width: 30px; height: 30px; border-radius: 50%; background: var(--sky); }

  .card-front {
    left: 590px; top: 440px;
    background: var(--paper);
  }
  .side-band { position: absolute; left: 0; top: 0; width: 42px; height: 100%; background: var(--navy); }
  .side-rule { position: absolute; left: 50px; top: 0; width: 3px; height: 100%; background: var(--sky); }
  .front-brand { position: absolute; left: 78px; top: 42px; display: flex; align-items: center; gap: 12px; }
  .front-brand .brand-name { color: var(--navy); font-size: 40px; font-weight: 700; letter-spacing: 5px; }
  .front-brand .brand-dot { width: 26px; height: 26px; border-radius: 50%; background: var(--sky); }
  .person { position: absolute; left: 78px; top: 118px; }
  .person-name { color: var(--sky); font-size: 23px; font-weight: 700; line-height: 1.1; }
  .person-role { color: var(--muted); font-size: 13px; margin-top: 2px; }
  .contact { position: absolute; font-size: 14px; color: var(--ink); list-style: none; }
  .contact li { display: flex; align-items: center; gap: 8px; height: 21px; white-space: nowrap; }
  .contact svg { width: 12px; height: 12px; fill: var(--sky); flex: none; }
  .contact-phones { left: 78px; top: 190px; }
  .contact-web { left: 290px; top: 190px; }
  .address { position: absolute; left: 78px; top: 254px; font-size: 14px; color: var(--ink); white-space: nowrap; }
</style>
</head>
<body>
  <section class="card card-back" aria-label="Business card back">
    <span class="brand-name">SkyvornQ</span>
    <span class="brand-dot"></span>
  </section>

  <section class="card card-front" aria-label="Business card front">
    <div class="side-band"></div>
    <div class="side-rule"></div>
    <div class="front-brand">
      <span class="brand-name">SkyvornQ</span>
      <span class="brand-dot"></span>
    </div>
    <div class="person">
      <p class="person-name">Dara Velling</p>
      <p class="person-role">Managing Director</p>
    </div>
    <ul class="contact contact-phones">
      <li><svg viewBox="0 0 12 12"><path d="M2.5 1l2 2-1 1.5a7 7 0 0 0 4 4l1.5-1 2 2-1.5 1.5C5 10.5 1.5 7 1 2.5z"/></svg>0412 5530 812</li>
      <li><svg viewBox="0 0 12 12"><path d="M3 0h6a1 1 0 0 1 1 1v10a1 1 0 0 1-1 1H3a1 1 0 0 1-1-1V1a1 1 0 0 1 1-1zm0 2v7h6V2z"/></svg>0455 7716 204</li>
    </ul>
    <ul class="contact contact-web">
      <li><svg viewBox="0 0 12 12"><path d="M0 2h12v8H0zm1 1v.3l5 3.4 5-3.4V3z"/></svg>dara@skyvornq.com</li>
      <li><svg viewBox="0 0 12 12"><circle cx="6" cy="6" r="6"/></svg>www.skyvornq.com</li>
    </ul>
    <p class="address">4827 Trellis Hollow Road, Brindlecove, Norvale 34951</p>
  </section>
</body>
</html>
```